Companybrochure for Consulting & Financing Firm

I need to have a Company Brochure asap for our company. We have a website that describes what we do, but we need also a brochure, that can be sent by PDF of eventually be printed as well.

The brochure should be short but nice and appealing to the customers.

We provide professional management consulting and help our customers to get finance for very diferent projects. Our business has a lot to do with personal relations, but also we are very professional in the way we work and how develop the solutions for our clients. Our clients are mainly government-owned firm, but also private trading companies and wealthy private investors.

Our customers are mainly in Latin America, but the company is headquater is in Switzerland. We are opening offices in Panama and Caracas, this should be easaly be adabtable later.

Please have a look at our website www.vorelpartners.ch. In the brochure, we would segment our services in 1.) Project Developments 2.) Management Conulting 3.) Investment Management and 4.) Finance Solutions.

Also do have a look at www.vorelpartners.ch
(Click E for the English version)
Updates

I managed to put the Mock-Up to the Website.
It is actually not really a mock-up, it is a version I have designed myself.
Well as I am not a designer, I hope you can make it much better.
The content however is what I would put in any other design as well.

Target Market(s)

Top Management, Investors, Entrepreneurs, Government Officials

Industry/Entity Type

Management Consulting

Requirements
Must have
• Design should reflect this image elements:

We are entrepreneurs.
We are comitted to get things done.
We work closely with the client side by side.
We are a professional partner.
We are not afraid of delivering unconventional solutions.
We look at the problem from various angles.
We analyse, develop solutions and implent results.
Should not have
• Typical US-American style elements. We do not want to give the impression of being a US company.

We do not want to appear to be neo-liberal. We are a politically neutral professional consulting firm.

```html
<!DOCTYPE html>
<html lang="en">
<head>
<meta charset="utf-8">
<title>Vorel Partners AG – Management Consulting</title>
<link rel="stylesheet" href="https://fonts.googleapis.com/css2?family=Inter+Tight:wght@300;800&family=Open+Sans:wght@400;600;700&display=swap">
<style>
  :root {
    --purple: #5c4a7b;
    --purple-deep: #4b3b69;
    --ink: #111111;
    --logo-grey: #333333;
    --paper: #ffffff;
    --photo-light: #b8b8b8;
    --photo-dark: #3a3a3a;
  }
  * { box-sizing: border-box; margin: 0; padding: 0; }
  html, body {
    width: 1200px; height: 860px; overflow: hidden;
    background: var(--paper);
  }
  .brochure-page {
    position: relative; width: 1200px; height: 860px;
    background: var(--paper);
    font-family: "Open Sans", Arial, sans-serif;
    color: var(--ink);
  }
  .top-rule {
    position: absolute; left: 0; top: 45px; width: 1200px; height: 11px;
    background: var(--ink);
  }
  .brand-name {
    position: absolute; right: 32px; top: 104px;
    font-family: "Open Sans", Arial, sans-serif;
    font-weight: 700; font-size: 41px; letter-spacing: -0.5px;
    color: var(--logo-grey);
  }
  .hero-banner {
    position: absolute; left: 0; top: 181px; width: 1200px; height: 275px;
  }
  .hero-banner svg { display: block; }
  .hero-title {
    position: absolute; left: 40px; top: 123px;
    font-family: "Inter Tight", Arial, sans-serif;
    color: #ffffff; text-transform: uppercase;
    line-height: 0.78; letter-spacing: -0.07em;
  }
  .hero-title .line-light { display: block; font-weight: 300; font-size: 76px; }
  .hero-title .line-bold { display: block; font-weight: 800; font-size: 76px; }

  .intro {
    position: absolute; left: 31px; top: 485px; width: 690px;
  }
  .intro-lead {
    color: var(--purple); font-weight: 700; font-size: 21.5px; line-height: 28px;
  }
  .principle-label {
    margin-top: 14px; font-weight: 700; font-size: 16.5px;
  }
  .process-chain { display: block; margin: 10px 0 0 74px; }
  .process-chain text {
    font-family: "Open Sans", Arial, sans-serif; font-weight: 700;
    font-size: 15px; fill: #ffffff;
  }
  .team-text {
    margin-top: 10px; font-weight: 700; font-size: 16.5px; line-height: 23px;
    text-align: justify;
  }
  .experts-text {
    margin-top: 13px; font-weight: 700; font-size: 16px;
  }

  .testimonials {
    position: absolute; left: 732px; top: 486px; width: 435px; height: 320px;
    background: var(--purple);
  }
  .testimonials-head {
    position: relative; height: 47px; background: var(--ink);
    color: #ffffff; font-weight: 700; font-size: 17px;
    display: flex; align-items: center; justify-content: center;
  }
  .testimonials-head::before {
    content: ""; position: absolute; left: 0; top: 0;
    border-top: 22px solid var(--purple); border-right: 22px solid transparent;
  }
  .testimonials-body {
    padding: 21px 14px 0 14px;
    color: #ffffff; font-size: 14.3px; line-height: 23.8px;
    text-align: justify;
  }
</style>
</head>
<body>
<div class="brochure-page">
  <div class="top-rule"></div>
  <div class="brand-name">Vorel Partners AG</div>

  <div class="hero-banner">
    <svg width="1200" height="275" viewBox="0 0 1200 275" role="img" aria-label="Black and white photograph of sailing yachts racing on open water, cut by diagonal black and purple bands">
      <defs>
        <linearGradient id="sea-photo" x1="0" y1="0" x2="0" y2="1">
          <stop offset="0" stop-color="var(--photo-dark)"/>
          <stop offset="0.55" stop-color="#7a7a7a"/>
          <stop offset="0.75" stop-color="var(--photo-light)"/>
          <stop offset="1" stop-color="#8c8c8c"/>
        </linearGradient>
      </defs>
      <rect width="1200" height="275" fill="url(#sea-photo)"/>
      <polygon points="165,0 787,0 599,275 -23,275" fill="var(--ink)"/>
      <polygon points="42,180 664,180 599,275 -23,275" fill="var(--purple-deep)"/>
      <polygon points="1017,0 1200,0 1200,275 829,275" fill="var(--ink)"/>
      <polygon points="894,180 1200,180 1200,275 829,275" fill="var(--purple-deep)"/>
    </svg>
    <h1 class="hero-title">
      <span class="line-light">Management</span>
      <span class="line-bold">Consulting</span>
    </h1>
  </div>

  <section class="intro">
    <p class="intro-lead">We elaborate solutions together with our customers and business partners by assisting owners and top management in structured decision making.</p>
    <p class="principle-label">We work goal-oriented following the principle:</p>
    <svg class="process-chain" width="550" height="36" viewBox="0 0 550 36" aria-label="Analysis, Solutions, Results">
      <polygon points="0,0 165,0 183,18 165,36 0,36 18,18" fill="var(--purple)"/>
      <polygon points="180,0 345,0 363,18 345,36 180,36 198,18" fill="var(--purple)"/>
      <polygon points="360,0 525,0 543,18 525,36 360,36 378,18" fill="var(--purple)"/>
      <text x="93" y="23.5" text-anchor="middle">ANALYSIS</text>
      <text x="273" y="23.5" text-anchor="middle">SOLUTIONS</text>
      <text x="453" y="23.5" text-anchor="middle">RESULTS</text>
    </svg>
    <p class="team-text">Our consulting team members do all have many years of experience from previous assignments at leading international management consulting companies and are familiar with methodologies used in management consulting.</p>
    <p class="experts-text">We complete the team of consultants with the appropriate subject matter experts.</p>
  </section>

  <aside class="testimonials">
    <h2 class="testimonials-head">WHAT OUR CLIENTS HAVE TO SAY...</h2>
    <p class="testimonials-body">Lorem Ipsum is simply dummy text of the printing and typesetting industry. Lorem Ipsum has been the industry's standard dummy text ever since the 1500s, when an unknown printer took a galley of type and scrambled it to make a type specimen book. It has survived not only five centuries, but also the leap into electronic typesetting, remaining essentially unchanged. It was popularised in the 1960s with the release of Letraset sheets containing Lorem Ipsum passages, and more recently with desktop publishing software like</p>
  </aside>
</div>
</body>
</html>
```